OpenHarbor Yoga Website Design

Business Logo - attached
5 pages being:
Home
About
Classes
Blog
Contact

Would like Scrolling webpage and yoga symbols to be used.

Must have's being:
Easy to navigate, Text needs to be able to be edited/updated, Enquire Now Links, More Information Links, be a secure site, SEO,

Please refer to attached document for the information for the body of the website.

Target Market(s)

Educators, Community Service, Health and Wellbeing, Mental Health

Industry/Entity Type

Yoga

Coding

Coded - Design and coding required

Number of Pages Required

5+ page

Font styles to use
Other font styles liked:
• Bella Bold BC

Colors
0094D4
00A9DD
6FCCEA
C7EBF8
E9F6FB
6B429C
8869AF
B7A5CE
E3DAEB
F3F0F8

Requirements
Must have
• Easy to navigate, Text needs to be able to be edited/updated, Enquire Now Links, More Information Links, be a secure site, SEO,
Nice to have
• Scrolling webpage, yoga symbols

```html
<!DOCTYPE html>
<html lang="en">
<head>
<meta charset="utf-8">
<title>OpenHarbor Yoga</title>
<link href="https://fonts.googleapis.com/css2?family=Nunito:wght@300;400;600;700;800&family=Kaushan+Script&display=swap" rel="stylesheet">
<style>
:root{
  --blue:#0094D4;
  --blue-2:#00A9DD;
  --sky:#E9F6FB;
  --purple:#6B429C;
  --purple-mid:#8869AF;
  --purple-soft:#B7A5CE;
  --lilac:#E3DAEB;
  --lilac-bg:#F0ECF7;
  --text:#4a4a55;
  --white:#ffffff;
}
*{margin:0;padding:0;box-sizing:border-box}
html,body{width:1200px;height:3495px;overflow:hidden}
body{position:relative;font-family:'Nunito',sans-serif;color:var(--text);background:var(--white)}
.abs{position:absolute}
.script{font-family:'Kaushan Script',cursive;color:var(--purple-mid);font-weight:400}

/* hero */
.hero{left:0;top:0;width:1200px;height:732px;background:var(--lilac-bg);overflow:hidden}
.brand{left:111px;top:40px;width:140px;display:flex;flex-direction:column;align-items:center;gap:8px}
.brand-dot{width:46px;height:46px;border-radius:50%;background:var(--purple-soft)}
.brand-name{font-size:17px;font-weight:700;color:var(--purple);text-align:center;line-height:1.15}
.nav{top:38px;left:560px;display:flex;gap:0}
.nav a{position:absolute;font-size:13px;font-weight:600;color:#222;text-decoration:none;white-space:nowrap}
.nav a.active{color:var(--purple-mid)}
.call{left:915px;top:30px;width:173px;height:36px;border-radius:18px;background:linear-gradient(90deg,var(--purple),var(--purple-soft));color:#fff;font-size:13px;font-weight:700;display:flex;align-items:center;justify-content:center;gap:6px;box-shadow:0 6px 14px rgba(107,66,156,.25)}
.hero-disc{left:343px;top:108px;width:516px;height:516px;border-radius:50%;background:#fff}
.hero-photo{left:300px;top:255px;width:560px;height:395px;border-radius:48% 52% 40% 40%;background:linear-gradient(160deg,#cfe7ec,#b9c8cc 55%,#e7d9cf)}
.dots span{position:absolute;border-radius:50%;background:var(--purple-soft)}
.hero-title{left:108px;top:232px;font-size:92px;line-height:1.2}
.hero-copy{left:111px;top:358px;width:345px;font-size:15px;line-height:21.5px;color:#555}
.btn{left:111px;top:448px;width:139px;height:37px;border-radius:19px;background:linear-gradient(90deg,var(--purple),var(--purple-soft));color:#fff;font-size:13px;font-weight:800;display:flex;align-items:center;justify-content:center}
.social-side{left:1136px;top:270px}
.social-side span{position:absolute;left:0;width:14px;height:14px;border-radius:50%;background:#333}
.scroll-cue{left:580px;top:712px;width:40px;height:40px;border-radius:50%;background:#fff;display:flex;align-items:center;justify-content:center}

/* welcome */
.welcome-mark{left:195px;top:858px;width:330px;height:330px;border-radius:50%;background:linear-gradient(135deg,var(--purple) ,var(--purple-soft) 70%,var(--lilac));display:flex;align-items:center;justify-content:center}
.welcome-mark span{font-size:30px;font-weight:700;color:#fff;text-align:center;line-height:1.2}
.eyebrow{left:599px;top:836px;font-size:18px;color:#333}
.welcome-title{left:597px;top:860px;font-size:66px;line-height:1.2}
.welcome-copy{left:599px;top:957px;width:470px;font-size:14.5px;line-height:21.5px;text-align:justify;color:#555}
.welcome-copy p+p{margin-top:21px}
.vert-word{font-weight:200;color:#eeeef2;letter-spacing:14px;white-space:nowrap}
.welcome-vert{left:1110px;top:739px;font-size:66px;writing-mode:vertical-rl}

/* benefits */
.benefits{left:0;top:1334px;width:1200px;height:1625px;background:linear-gradient(180deg,var(--sky),#eaf2fb 60%,var(--sky))}
.benefits-vert{left:36px;top:1573px;font-size:64px;color:#c9dcea;writing-mode:vertical-rl;transform:rotate(180deg);letter-spacing:16px;font-weight:200}
.benefits-title{left:0;width:1200px;top:1430px;text-align:center;font-size:68px;line-height:1.2}
.center-copy{left:195px;width:810px;text-align:center;font-size:14.5px;line-height:21.5px;color:#444}
.block-title{font-size:31px;font-weight:700;color:var(--blue)}
.ticks{list-style:none;width:400px}
.ticks li{position:relative;padding-left:31px;font-size:14.5px;line-height:18px;color:#444;margin-bottom:16px}
.ticks li svg{position:absolute;left:0;top:1px}
.ring{border-radius:50%}
.photo{border-radius:50%}
.badge{width:96px;height:96px;border-radius:50%;background:#f4f1fa;box-shadow:0 6px 18px rgba(107,66,156,.18);display:flex;align-items:center;justify-content:center}

/* footer */
.footer{left:0;top:2959px;width:1200px;height:536px;background:var(--purple-mid)}
.card{top:3033px;width:312px;height:113px;background:#a18bcb;display:flex;align-items:center;padding-left:30px;gap:20px;color:#fff}
.card .ico{width:56px;height:56px;border-radius:50%;background:#fff;display:flex;align-items:center;justify-content:center;flex:none}
.card small{display:block;font-size:14px;margin-bottom:6px}
.card b{font-size:14px;font-weight:700;line-height:20px;display:block}
.foot-brand{left:0;width:1200px;top:3200px;display:flex;flex-direction:column;align-items:center;gap:12px}
.foot-brand .brand-dot{width:60px;height:60px;background:var(--lilac)}
.foot-brand .brand-name{color:#fff;font-size:22px}
.foot-nav{left:0;width:1200px;top:3378px;text-align:center;font-size:13px;font-weight:800;color:#fff;letter-spacing:.3px}
.foot-nav i{font-style:normal;margin:0 14px}
.rule{left:0;top:3431px;width:1200px;border-top:2px dotted rgba(255,255,255,.7)}
.foot-social span{position:absolute;top:3450px;width:24px;height:24px;border-radius:50%;background:#a18bcb}
.copy{left:760px;width:330px;text-align:right;top:3454px;font-size:13px;color:#fff}
</style>
</head>
<body>

<!-- Hero -->
<section class="abs hero">
  <div class="abs hero-disc"></div>
  <div class="abs hero-photo" role="img" aria-label="Photo of a woman in a low lunge yoga pose"></div>
  <div class="dots">
    <span style="left:778px;top:130px;width:11px;height:11px"></span>
    <span style="left:807px;top:150px;width:16px;height:16px"></span>
    <span style="left:832px;top:176px;width:19px;height:19px"></span>
    <span style="left:851px;top:209px;width:19px;height:19px"></span>
    <span style="left:865px;top:245px;width:16px;height:16px"></span>
    <span style="left:874px;top:285px;width:11px;height:11px"></span>
  </div>
</section>

<div class="abs brand">
  <div class="brand-dot"></div>
  <div class="brand-name">OpenHarbor<br>Yoga</div>
</div>

<nav class="abs nav">
  <a class="active" href="#" style="left:0">Home</a>
  <a href="#" style="left:65px">About</a>
  <a href="#" style="left:130px">Classes</a>
  <a href="#" style="left:206px">Blog</a>
  <a href="#" style="left:262px">Contact</a>
</nav>
<div class="abs call">
  <svg width="12" height="12" viewBox="0 0 24 24"><path fill="#fff" d="M6.6 10.8a15 15 0 0 0 6.6 6.6l2.2-2.2c.3-.3.7-.4 1-.2 1.1.4 2.3.6 3.6.6.6 0 1 .4 1 1V20c0 .6-.4 1-1 1A17 17 0 0 1 3 4c0-.6.4-1 1-1h3.5c.6 0 1 .4 1 1 0 1.3.2 2.5.6 3.6.1.3 0 .7-.2 1z"/></svg>
  +1 555 010 0199
</div>

<h1 class="abs script hero-title">OpenHarbor</h1>
<p class="abs hero-copy">Lorem ipsum dolor sit amet, consectetur adipiscing elit, sed do eiusmod tempor incididunt ut labore et dolore magna aliqua.</p>
<a class="abs btn">GET A QUOTE</a>

<div class="abs social-side">
  <span style="top:0"></span><span style="top:43px"></span><span style="top:85px"></span><span style="top:129px"></span>
</div>

<div class="abs scroll-cue">
  <svg width="16" height="16" viewBox="0 0 16 16"><path d="M3 3l5 4 5-4M3 8l5 4 5-4" fill="none" stroke="#222" stroke-width="1.8"/></svg>
</div>

<!-- Welcome -->
<div class="abs welcome-mark"><span>OpenHarbor<br>Yoga</span></div>
<p class="abs eyebrow">Welcome to</p>
<h2 class="abs script welcome-title">OpenHarbor Yoga</h2>
<div class="abs welcome-copy">
  <p>OpenHarbor Yoga believe that you are never too young to benefit from and fall in love with yoga. My aim is to EMPOWER kids and teens to thrive by teaching life skills in Yoga, Mindfulness and Breathing techniques to deal with daily challenges and big emotions.</p>
  <p>OpenHarbor Yoga gives kids an opportunity to enjoy and experience yoga for themselves and primarily focuses on programs for Schools, Pre Schools and Early Learning Centres, Private Classes, Sporting Clubs, Martial Arts Schools, Scout Groups and Occupational Therapy Centres just to name a few. All classes are age appropriate and encourage children's natural drive to learn, move, and be creative.</p>
</div>
<div class="abs vert-word welcome-vert">WELCOME</div>

<!-- Benefits -->
<section class="abs benefits"></section>
<div class="abs benefits-vert">BENEFITS OF YOGA</div>
<h2 class="abs script benefits-title">Benefits of Yoga</h2>
<p class="abs center-copy" style="top:1535px">The benefits of yoga can last a lifetime. It is my aim &amp; passion to introduce yoga to kids of all ages and backgrounds so that they can not only experience the benefits of yoga but fall in love with the practice.</p>

<svg width="0" height="0" style="position:absolute">
  <defs>
    <linearGradient id="ringGrad" x1="0" y1="0" x2="0" y2="1">
      <stop offset="0" stop-color="#0094D4"/><stop offset="1" stop-color="#6B429C"/>
    </linearGradient>
    <symbol id="tick" viewBox="0 0 16 16">
      <circle cx="8" cy="8" r="6.6" fill="none" stroke="#8869AF" stroke-width="1.3"/>
      <path d="M5 8.2l2.1 2 3.9-4" fill="none" stroke="#8869AF" stroke-width="1.4"/>
    </symbol>
  </defs>
</svg>

<!-- Healthy Bodies -->
<h3 class="abs block-title" style="left:178px;top:1620px">Healthy Bodies</h3>
<ul class="abs ticks" style="left:180px;top:1675px">
  <li><svg width="16" height="16"><use href="#tick"/></svg>Develops strong, flexible and healthy bodies</li>
  <li><svg width="16" height="16"><use href="#tick"/></svg>Promotes spinal alignment and good posture</li>
  <li><svg width="16" height="16"><use href="#tick"/></svg>Builds energy and stamina</li>
  <li><svg width="16" height="16"><use href="#tick"/></svg>Improves internal physical function - organs, digestion, elimination, circulation, and blood flow.</li>
  <li><svg width="16" height="16"><use href="#tick"/></svg>Helps breathing and lung capacity</li>
  <li><svg width="16" height="16"><use href="#tick"/></svg>Teaches the enjoyment of movement</li>
  <li><svg width="16" height="16"><use href="#tick"/></svg>Works the 'whole' body</li>
</ul>
<svg class="abs" style="left:712px;top:1614px" width="312" height="312"><circle cx="156" cy="156" r="150" fill="#fff" stroke="url(#ringGrad)" stroke-width="6"/></svg>
<div class="abs photo" role="img" aria-label="Photo of a woman in a pigeon yoga pose" style="left:695px;top:1595px;width:330px;height:330px;border-radius:45% 45% 50% 50%;background:linear-gradient(170deg,#f3d5da,#e0a7b5 45%,#3a3a42)"></div>
<div class="abs badge" style="left:691px;top:1638px">
  <svg width="48" height="48" viewBox="0 0 48 48" fill="none" stroke="#6B8FD0" stroke-width="1.6"><circle cx="24" cy="11" r="5"/><path d="M24 17v14M16 22l8 4 8-4M10 36c6-5 22-5 28 0M12 40h24"/></svg>
</div>

<!-- Healthy Minds -->
<svg class="abs" style="left:176px;top:1987px" width="312" height="312"><circle cx="156" cy="156" r="150" fill="#fff" stroke="url(#ringGrad)" stroke-width="6"/></svg>
<div class="abs photo" role="img" aria-label="Photo of a woman seated cross-legged in meditation" style="left:165px;top:1950px;width:350px;height:345px;border-radius:45% 45% 50% 50%;background:linear-gradient(175deg,#e8d0c4,#d2b2a2 40%,#2c2c33 62%,#8a8c94)"></div>
<div class="abs badge" style="left:413px;top:2009px">
  <svg width="48" height="48" viewBox="0 0 48 48" fill="none" stroke="#6B8FD0" stroke-width="1.6"><path d="M24 8c5 5 5 12 0 17-5-5-5-12 0-17zM12 14c7 1 11 6 12 11-7 0-12-5-12-11zM36 14c-7 1-11 6-12 11 7 0 12-5 12-11z"/><circle cx="24" cy="30" r="3"/><path d="M24 33v5M14 40c5-4 15-4 20 0"/></svg>
</div>
<h3 class="abs block-title" style="left:612px;top:1992px">Healthy Minds</h3>
<ul class="abs ticks" style="left:614px;top:2047px">
  <li><svg width="16" height="16"><use href="#tick"/></svg>Cultivates confidence and self-esteem</li>
  <li><svg width="16" height="16"><use href="#tick"/></svg>Develops concentration and attention</li>
  <li><svg width="16" height="16"><use href="#tick"/></svg>Clears the mind for better clarity and decision making</li>
  <li><svg width="16" height="16"><use href="#tick"/></svg>Helps relax and sleep better</li>
  <li><svg width="16" height="16"><use href="#tick"/></svg>Calms the nervous system</li>
  <li><svg width="16" height="16"><use href="#tick"/></svg>Learns to cope with stressful situations</li>
  <li><svg width="16" height="16"><use href="#tick"/></svg>Balances emotions</li>
</ul>

<!-- Healthy Spirits -->
<h3 class="abs block-title" style="left:178px;top:2366px">Healthy Spirits</h3>
<ul class="abs ticks" style="left:180px;top:2421px">
  <li><svg width="16" height="16"><use href="#tick"/></svg>Fosters creativity, expression and imagination</li>
  <li><svg width="16" height="16"><use href="#tick"/></svg>Cultivates kindness to themselves and others</li>
  <li><svg width="16" height="16"><use href="#tick"/></svg>Cultivates respect for self and others</li>
  <li><svg width="16" height="16"><use href="#tick"/></svg>Builds balance and inner quiet</li>
  <li><svg width="16" height="16"><use href="#tick"/></svg>Builds inner strength and resilience</li>
  <li><svg width="16" height="16"><use href="#tick"/></svg>Teaches self-awareness</li>
  <li><svg width="16" height="16"><use href="#tick"/></svg>Focuses on positive self-talk</li>
</ul>
<svg class="abs" style="left:712px;top:2359px" width="312" height="312"><circle cx="156" cy="156" r="150" fill="#fff" stroke="url(#ringGrad)" stroke-width="6"/></svg>
<div class="abs photo" role="img" aria-label="Photo of a woman in a seated twist yoga pose" style="left:695px;top:2345px;width:360px;height:330px;border-radius:45% 45% 50% 50%;background:linear-gradient(170deg,#efd6cc,#9c7384 45%,#6e4d5e)"></div>
<div class="abs badge" style="left:691px;top:2383px">
  <svg width="48" height="48" viewBox="0 0 48 48" fill="none" stroke="#6B8FD0" stroke-width="1.6"><circle cx="22" cy="12" r="4"/><path d="M22 16v14l-2 12M22 20l12-8M22 22l-10 4M20 30l8 2M12 42h24"/></svg>
</div>

<div class="abs center-copy" style="top:2716px">
  <p>OpenHarbor Yoga combines all the benefits of traditional yoga and a lot of fun!<br>We play games and practice engaging flows which get our bodies moving, then we take a quiet moment to be still and calm as we focus on our breathing.</p>
  <p style="margin-top:21px">OpenHarbor Yoga Kids will learn that relaxation is just as important as moving their bodies, and the exercises which they learn in class can easily be repeated at any time in their busy day to feel calm and grounded.</p>
</div>

<!-- Footer -->
<footer class="abs footer"></footer>
<div class="abs card" style="left:111px">
  <div class="ico"><svg width="20" height="24" viewBox="0 0 20 24"><path fill="#8869AF" d="M10 0a8 8 0 0 0-8 8c0 6 8 16 8 16s8-10 8-16a8 8 0 0 0-8-8zm0 11a3 3 0 1 1 0-6 3 3 0 0 1 0 6z"/></svg></div>
  <div><small>Location :</small><b>Kestrel Bay, Victoria<br>Australia 3999</b></div>
</div>
<div class="abs card" style="left:443px">
  <div class="ico"><svg width="20" height="20" viewBox="0 0 24 24"><path fill="#8869AF" d="M6.6 10.8a15 15 0 0 0 6.6 6.6l2.2-2.2c.3-.3.7-.4 1-.2 1.1.4 2.3.6 3.6.6.6 0 1 .4 1 1V20c0 .6-.4 1-1 1A17 17 0 0 1 3 4c0-.6.4-1 1-1h3.5c.6 0 1 .4 1 1 0 1.3.2 2.5.6 3.6.1.3 0 .7-.2 1z"/></svg></div>
  <div><small>Phone :</small><b>0400 555 018</b></div>
</div>
<div class="abs card" style="left:776px">
  <div class="ico"><svg width="22" height="16" viewBox="0 0 22 16"><rect width="22" height="16" rx="2" fill="#8869AF"/><path d="M1 2l10 7 10-7" fill="none" stroke="#fff" stroke-width="1.6"/></svg></div>
  <div><small>Email :</small><b>hello@openharboryoga.example</b></div>
</div>

<div class="abs foot-brand">
  <div class="brand-dot"></div>
  <div class="brand-name">OpenHarbor Yoga</div>
</div>

<div class="abs foot-nav">HOME<i>|</i>ABOUT<i>|</i>CLASSES<i>|</i>BLOG<i>|</i>CONTACT</div>
<div class="abs rule"></div>
<div class="foot-social"><span style="left:111px"></span><span style="left:144px"></span></div>
<div class="abs copy">© Copyrights 2023 | All Rights Reserved</div>

</body>
</html>
```